Redesign of business card for Cedar Ridge Mechanical

We are looking for a new design for our business cards for Cedar Ridge Mechanical. We are a plumbing & HVAC construction company, operating on the West Coast of Canada and USA. Logo attached.
Industry/Entity Type
Construction - Plumbing & HVAC
Contact Information for Business Card
Name, address, phone numbers, email, website address
Look and feel
Each slider illustrates characteristics of the customer's brand and the style your logo design should communicate.

```html
<!DOCTYPE html>
<html lang="en">
<head>
<meta charset="utf-8">
<title>Cedar Ridge Mechanical — Business Card</title>
<link href="https://fonts.googleapis.com/css2?family=Montserrat:wght@400;500;700;800&display=swap" rel="stylesheet">
<style>
  :root {
    --stage: #2b2b2d;
    --card-white: #ffffff;
    --card-black: #121213;
    --ink: #141414;
    --ink-soft: #6f6f6f;
    --rule: #5a5a5a;
    --accent-grey: #3a3a3c;
    --back-mark: #55575a;
  }
  * { box-sizing: border-box; margin: 0; padding: 0; }
  html, body { width: 1200px; height: 801px; overflow: hidden; }
  body {
    background: var(--stage);
    font-family: "Montserrat", sans-serif;
    position: relative;
  }
  .card {
    position: absolute;
    top: 250px;
    width: 525px;
    height: 300px;
    border-radius: 16px;
    overflow: hidden;
  }
  .card-front { left: 50px; background: var(--card-white); color: var(--ink); }
  .card-back { left: 625px; background: var(--card-black); }

  .front-corner-tab {
    position: absolute; top: 0; right: 0;
    width: 34px; height: 16px;
    background: var(--card-black);
    border-bottom-left-radius: 6px;
  }
  .front-corner-block {
    position: absolute; right: 0; bottom: 0;
    width: 70px; height: 118px;
    background: var(--accent-grey);
    border-top-left-radius: 4px;
  }

  .brand {
    position: absolute; left: 34px; top: 92px;
    display: flex; align-items: center; gap: 12px;
  }
  .brand-square {
    width: 40px; height: 40px;
    border: 5px solid var(--ink);
    border-radius: 4px;
  }
  .brand-name {
    font-weight: 800; font-size: 17px; line-height: 1.15;
    letter-spacing: 0.5px; text-transform: uppercase; color: var(--ink);
  }

  .person { position: absolute; right: 44px; top: 30px; text-align: right; }
  .person-name { font-weight: 800; font-size: 17px; letter-spacing: 0.8px; }
  .person-name .surname { color: var(--ink-soft); }
  .person-role { font-size: 11px; font-weight: 500; margin-top: 2px; }

  .rule { position: absolute; height: 1px; background: var(--rule); }
  .rule-top { left: 250px; right: 44px; top: 80px; }
  .rule-mid { left: 34px; right: 110px; top: 218px; }

  .contact {
    position: absolute; font-size: 12.5px; color: var(--ink);
    display: flex; align-items: center; gap: 7px; white-space: nowrap;
  }
  .contact svg { width: 11px; height: 11px; fill: var(--ink); flex: none; }
  .contact-address { left: 34px; top: 196px; color: var(--ink-soft); }
  .contact-phone { left: 34px; top: 228px; }
  .contact-email { left: 34px; top: 254px; }
  .contact-web { left: 250px; top: 254px; }

  .back-brand {
    position: absolute; inset: 0;
    display: flex; align-items: center; justify-content: center; gap: 18px;
  }
  .back-square {
    width: 58px; height: 58px;
    border: 7px solid var(--back-mark); border-radius: 6px;
  }
  .back-name {
    font-weight: 800; font-size: 24px; line-height: 1.2;
    letter-spacing: 1px; text-transform: uppercase; color: var(--back-mark);
  }
</style>
</head>
<body>
  <section class="card card-front">
    <div class="front-corner-tab"></div>
    <div class="front-corner-block"></div>

    <div class="brand">
      <div class="brand-square"></div>
      <div class="brand-name">Cedar Ridge<br>Mechanical</div>
    </div>

    <div class="person">
      <div class="person-name">DANIEL <span class="surname">HARPER</span></div>
      <div class="person-role">Manager</div>
    </div>
    <div class="rule rule-top"></div>

    <div class="contact contact-address">Your address, city, state, ZIP 0000</div>
    <div class="rule rule-mid"></div>
    <div class="contact contact-phone">
      <svg viewBox="0 0 24 24"><path d="M6.6 10.8a15.1 15.1 0 0 0 6.6 6.6l2.2-2.2a1 1 0 0 1 1-.25 11.4 11.4 0 0 0 3.6.57 1 1 0 0 1 1 1V20a1 1 0 0 1-1 1A17 17 0 0 1 3 4a1 1 0 0 1 1-1h3.5a1 1 0 0 1 1 1c0 1.25.2 2.45.57 3.57a1 1 0 0 1-.25 1z"/></svg>
      123-456-2100
    </div>
    <div class="contact contact-email">
      <svg viewBox="0 0 24 24"><path d="M2 5h20v14H2zm2 2v.5l8 5 8-5V7zm0 3v7h16v-7l-8 5z"/></svg>
      youremail@mailbox.com
    </div>
    <div class="contact contact-web">
      <svg viewBox="0 0 24 24"><circle cx="12" cy="12" r="10"/></svg>
      www.yourwebsite.com
    </div>
  </section>

  <section class="card card-back">
    <div class="back-brand">
      <div class="back-square"></div>
      <div class="back-name">Cedar Ridge<br>Mechanical</div>
    </div>
  </section>
</body>
</html>
```